New Brochure Design Project

We need a fresh, professional and modern brochure design template that we can use to communicate our products and services to our customers.
The Brochure has to fit to our corporate style which can be found at: www.dravolent.nl
Our products can be found at: www.shop.dravolent.nl

The brochure has to be in A-4 format and has to contain:
- one front
- two different content pages (tekst and photo's)
- one back

Goodluck,

Team Dravolent.

```html
<!DOCTYPE html>
<html lang="en">
<head>
<meta charset="utf-8">
<title>Dravolent Brochure Presentation</title>
<link rel="stylesheet" href="https://fonts.googleapis.com/css2?family=Source+Sans+3:wght@300;400;600&display=swap">
<style>
:root{
  --orange:#f08a1c;
  --orange-deep:#e8731a;
  --amber:#fbb040;
  --cream:#ffd98a;
  --night:#1c1c1c;
  --ink:#333;
  --ink-head:#444;
  --ink-soft:#777;
  --paper:#fff;
  --frame:#222;
}
*{box-sizing:border-box;margin:0;padding:0}
html,body{width:1200px;height:900px;overflow:hidden;background:var(--paper);font-family:"Source Sans 3",Arial,sans-serif}
.board{position:relative;width:1200px;height:900px}

.zoom{position:absolute;overflow:hidden;border:1px solid var(--frame)}
.zoom-back{left:82px;top:18px;width:472px;height:431px;background:var(--night)}
.zoom-inner{left:82px;top:457px;width:472px;height:430px;background:var(--paper)}
.zoom svg.bg{position:absolute;inset:0}

.contact{position:absolute;left:98px;top:5px;color:#ddd;font-weight:300;font-size:17px;line-height:21.5px}
.contact .gap{height:21px}
.contact-line{display:flex;align-items:center;gap:6px;margin-left:-22px}
.contact-line svg{width:16px;height:16px;flex:none}

.feature{position:absolute;left:50px;width:520px}
.feature-head{display:flex;align-items:center;gap:14px;font-weight:300;font-size:31px;color:var(--ink-head);height:44px;white-space:nowrap}
.feature-head svg{width:36px;height:36px;flex:none}
.feature-rule{height:1px;background:var(--amber);width:520px;margin:2px 0 11px}
.feature p{font-size:16.5px;line-height:20px;color:var(--ink);white-space:nowrap}
.feature p+p{margin-top:20px}
.feature p.cont{margin-top:0}

.connector{position:absolute;left:0;top:0;pointer-events:none}
.lens{position:absolute;width:26px;height:26px;border:1px solid #555;background:var(--paper)}

.thumb{position:absolute;box-shadow:0 2px 6px rgba(0,0,0,.35);overflow:hidden}
.cover{left:672px;top:65px;width:446px;height:315px;background:var(--night)}
.cover svg{position:absolute;inset:0}
.cover-address{position:absolute;left:22px;top:218px;font-size:4px;line-height:5px;color:#aaa}
.cover-brand{position:absolute;left:238px;top:213px;display:flex;align-items:center;gap:5px;color:var(--paper);font-size:15px;font-weight:400}
.cover-brand .dot{width:12px;height:12px;border-radius:50%;background:var(--orange)}
.cover-url{position:absolute;left:264px;top:240px;font-size:5px;color:#bbb}

.spread{left:672px;top:517px;width:446px;height:316px;background:var(--paper)}
.spread svg.bg{position:absolute;inset:0}
.col{position:absolute;width:182px;font-size:4.1px;line-height:5.5px;color:var(--ink-soft)}
.col-left{left:21px;top:54px}
.col h3{font-size:6.4px;line-height:8px;font-weight:400;color:var(--ink)}
.col .lead{color:var(--orange);font-size:4.4px;line-height:5.8px;margin:1px 0 3px}
.col p{margin-bottom:3px}
.mini-section{margin-top:4px;border-bottom:.5px solid var(--amber);padding-bottom:1px;margin-bottom:2px;font-size:5px;line-height:7px;color:var(--ink);display:flex;align-items:center;gap:3px}
.mini-section i{width:5px;height:5px;background:var(--orange);border-radius:50%;display:block}
.product{position:absolute;left:244px;width:182px}
.product-body{display:flex;gap:5px;align-items:flex-start}
.product-frame{width:34px;height:46px;flex:none;border:.6px solid #ccc;padding:2px;background:var(--paper)}
.product-box{width:100%;height:100%;background:linear-gradient(135deg,#3a3a3a,#151515 55%,var(--orange))}
.product-text p{margin-bottom:2.5px}
.spread-foot{position:absolute;bottom:3px;font-size:4px;color:#ccc}
</style>
</head>
<body>
<main class="board">

  <section class="zoom zoom-back" aria-label="Back cover detail">
    <svg class="bg" viewBox="0 0 472 431" preserveAspectRatio="none">
      <defs>
        <linearGradient id="swoopBack" x1="0" y1="0" x2="1" y2="1">
          <stop offset="0" stop-color="#fbb040"/><stop offset="1" stop-color="#f07b1a"/>
        </linearGradient>
      </defs>
      <path d="M0 270 C120 330 300 395 472 420 L472 431 L0 431 Z" fill="#ffe08f"/>
      <path d="M0 282 C120 345 300 405 472 431 L0 431 Z" fill="url(#swoopBack)"/>
    </svg>
    <div class="contact">
      <div>Dravolent B.V.</div>
      <div>Lindenhofstraat 42b</div>
      <div>2031KP Haarlem</div>
      <div class="gap"></div>
      <div class="contact-line"><svg viewBox="0 0 16 16"><circle cx="8" cy="8" r="7" fill="none" stroke="#f08a1c" stroke-width="1.6"/><path d="M5 4l2 2-1 1.5c.6 1.3 1.3 2 2.5 2.5L10 9l2 2-1.5 1.5C7.5 12 4 8.5 3.5 5.5Z" fill="#f08a1c"/></svg>+31 (0)30 555 0148</div>
      <div class="contact-line"><svg viewBox="0 0 16 16"><rect x="1" y="4" width="14" height="10" fill="#f08a1c"/><path d="M1 4l7 6 7-6" fill="none" stroke="#1c1c1c" stroke-width="1.2"/></svg>info@dravolent.nl</div>
      <div class="contact-line"><svg viewBox="0 0 16 16"><g fill="none" stroke="#f08a1c" stroke-width="1.4"><circle cx="8" cy="8" r="6.8"/><ellipse cx="8" cy="8" rx="3" ry="6.8"/><path d="M1.2 8h13.6M2.5 4.5h11M2.5 11.5h11"/></g></svg>http://www.dravolent.nl</div>
    </div>
  </section>

  <section class="zoom zoom-inner" aria-label="Inner page detail">
    <div class="feature" style="top:20px">
      <div class="feature-head"><svg viewBox="0 0 36 36"><circle cx="18" cy="18" r="12" fill="none" stroke="#f08a1c" stroke-width="7" stroke-dasharray="4.2 2.1"/><circle cx="18" cy="18" r="9" fill="none" stroke="#f08a1c" stroke-width="4"/></svg>Agile Software Development</div>
      <div class="feature-rule"></div>
      <p>Dravolent develops high-standard Custom applications, Shopvane Modules and can</p>
      <p class="cont">integrate every platform that provides an API.</p>
      <p>We use Agile projectmanagement techniques like Scrum and Extreme Programming to get</p>
      <p class="cont">your Return on Investment as soon as possible.</p>
    </div>
    <div class="feature" style="top:199px">
      <div class="feature-head"><svg viewBox="0 0 36 36"><path d="M4 10h9a5 5 0 1 1 10 0h9v9a5 5 0 1 0 0 10v3H4v-9a5 5 0 1 0 0-10Z" fill="#f08a1c"/></svg>Shopvane Module Development</div>
      <div class="feature-rule"></div>
      <p>With our decade of experience in Shopvane Webshops, we know what is possible. If a</p>
      <p class="cont">Shopvane Module doesn't exist yet, we can create this module for you.</p>
    </div>
    <div class="feature" style="top:318px">
      <div class="feature-head"><svg viewBox="0 0 36 36"><rect x="2" y="10" width="32" height="22" rx="3" fill="#f08a1c"/><path d="M13 10V6h10v4" fill="none" stroke="#f08a1c" stroke-width="3"/></svg>Portfolio</div>
      <div class="feature-rule"></div>
      <p>Thanks to our experience with Agile Software Development, Modules and integrations we deliver</p>
      <p class="cont">incredible quality while the costs are kept as low as possible. Check our portfolio below.</p>
    </div>
  </section>

  <svg class="connector" width="1200" height="900" aria-hidden="true">
    <path d="M553 143L622 212M553 585L622 647" stroke="#555" stroke-width="1" fill="none"/>
  </svg>
  <svg class="lens" style="left:622px;top:212px" viewBox="0 0 26 26" aria-hidden="true"><circle cx="11" cy="11" r="6" fill="none" stroke="#111" stroke-width="2"/><path d="M15 15l6 6M8.5 8.5l5 5M13.5 8.5l-5 5" stroke="#111" stroke-width="2"/></svg>
  <svg class="lens" style="left:622px;top:647px" viewBox="0 0 26 26" aria-hidden="true"><circle cx="11" cy="11" r="6" fill="none" stroke="#111" stroke-width="2"/><path d="M15 15l6 6M8.5 8.5l5 5M13.5 8.5l-5 5" stroke="#111" stroke-width="2"/></svg>

  <section class="thumb cover" aria-label="Front and back cover">
    <svg viewBox="0 0 446 315" preserveAspectRatio="none">
      <defs>
        <linearGradient id="coverTop" x1="0" y1="0" x2="0" y2="1"><stop offset="0" stop-color="#e8731a"/><stop offset="1" stop-color="#fbb040"/></linearGradient>
        <linearGradient id="coverBottom" x1="0" y1="0" x2="0" y2="1"><stop offset="0" stop-color="#fbb040"/><stop offset="1" stop-color="#e8731a"/></linearGradient>
      </defs>
      <rect width="446" height="100" fill="url(#coverTop)"/>
      <path d="M0 58 Q110 72 223 92 Q336 72 446 58 L446 62 Q336 78 223 98 Q110 78 0 62 Z" fill="#ffe08f"/>
      <path d="M0 62 Q110 78 223 98 Q336 78 446 62 L446 315 L0 315 Z" fill="#1c1c1c"/>
      <rect x="223" y="95" width="223" height="220" fill="#202020"/>
      <path d="M0 266 Q120 300 223 308 Q336 300 446 270 L446 315 L0 315 Z" fill="#ffe08f"/>
      <path d="M0 272 Q120 306 223 315 L446 315 L446 276 Q336 306 223 315 L0 315 Z" fill="url(#coverBottom)"/>
    </svg>
    <div class="cover-address">Dravolent B.V.<br>Lindenhofstraat 42b<br>2031KP Haarlem<br><br>+31 (0)30 555 0148<br>info@dravolent.nl<br>http://www.dravolent.nl</div>
    <div class="cover-brand"><span class="dot"></span>Dravolent</div>
    <div class="cover-url">www.dravolent.nl</div>
  </section>

  <section class="thumb spread" aria-label="Inner content pages">
    <svg class="bg" viewBox="0 0 446 316" preserveAspectRatio="none">
      <path d="M0 0H446V14Q336 28 223 40Q110 28 0 16Z" fill="#f08a1c"/>
      <path d="M0 16Q110 28 223 40Q336 28 446 14V18Q336 32 223 44Q110 32 0 20Z" fill="#ffd98a"/>
      <path d="M0 298Q223 292 446 298V302H0Z" fill="#f08a1c"/>
      <rect y="302" width="446" height="14" fill="#1c1c1c"/>
    </svg>

    <div class="col col-left">
      <h3>About Us</h3>
      <div class="lead">Dravolent is a young, reliable and transparent web agency. We help merchants grow online by building shops, modules and custom software that simply work, today and tomorrow.</div>
      <p>We are a small team of developers and designers who have worked with online shops for more than ten years. Every project starts with a clear plan, short sprints and regular demos, so you always know where your budget goes and what you will receive next. We write clean code, test every change and document our work so your own staff can keep using it.</p>
      <p>Before we start a project, we sit down with you and map the goals of your business. Together we decide which features bring value first. After each sprint you review the result and steer the next step, which keeps risk low and lets you launch early.</p>
      <p>Our certified developers know the Shopvane platform inside out. They build modules, connect payment and stock systems and tune your shop for speed, so customers find products quickly and checkout stays smooth on every device.</p>
      <p>Curious what we can do for you? Call or mail us for a free first talk.</p>
      <div class="mini-section"><i></i>Agile Software Development</div>
      <p>Dravolent develops custom applications and Shopvane modules and can connect every platform that offers an API. Agile methods like Scrum keep your return on investment high.</p>
      <div class="mini-section"><i></i>Shopvane Module Development</div>
      <p>With ten years of Shopvane experience we know what is possible. If a module does not exist yet, we can build it for you.</p>
      <div class="mini-section"><i></i>Portfolio</div>
      <p>Our work shows fast delivery and high quality at a fair price. Ask for references or see recent projects on our website.</p>
      <div class="mini-section"><i></i>About us</div>
      <p>A small team of skilled developers who enjoy solving hard problems. We keep short lines with every client and answer questions quickly.</p>
      <div class="mini-section"><i></i>Support</div>
      <p>Need help after launch? We offer support contracts with fixed response times, updates and monitoring to keep your shop online.</p>
    </div>

    <article class="product col" style="top:54px">
      <h3>Shopvane Single Sign-On</h3>
      <div class="lead">Let customers log in once and reach every store and service you run. One account, one cart and one order history everywhere.</div>
      <div class="product-body">
        <div class="product-frame"><div class="product-box" role="img" aria-label="Product box of the single sign-on module"></div></div>
        <div class="product-text">
          <p>Single Sign-On links customer accounts across all your shops. Buyers sign in on one site and stay signed in on the others, which removes friction and raises conversion. The module works with common identity services and needs no changes to your theme.</p>
          <p>Setup takes less than an hour and all settings live in the familiar admin panel.</p>
        </div>
      </div>
      <p style="margin-top:3px">Available for all recent platform versions, with one year of free updates.</p>
    </article>

    <article class="product col" style="top:142px">
      <h3>Configurable Bundle</h3>
      <div class="lead">Combine configurable products into a single bundle with its own price, stock and images.</div>
      <div class="product-body">
        <div class="product-frame"><div class="product-box" role="img" aria-label="Product box of the configurable bundle module"></div></div>
        <div class="product-text">
          <p>Shoppers choose size, colour and other options for each item while the bundle stays simple to manage in the back office. Discounts apply automatically.</p>
          <p>Ideal for gift sets, outfits and starter kits that sell better together.</p>
        </div>
      </div>
    </article>

    <article class="product col" style="top:216px">
      <h3>Product Merge</h3>
      <div class="lead">Merge simple products into one clear configurable product without rebuilding your catalog.</div>
      <div class="product-body">
        <div class="product-frame"><div class="product-box" role="img" aria-label="Product box of the product merge module"></div></div>
        <div class="product-text">
          <p>Select the products you want to join, choose the attributes that differ and the module creates a single product page with every choice visible. Old links redirect to the new page.</p>
          <p>Fewer pages means a cleaner catalog, better search results and happier visitors.</p>
        </div>
      </div>
    </article>

    <div class="spread-foot" style="left:10px">Dravolent</div>
    <div class="spread-foot" style="right:10px">Dravolent</div>
  </section>

</main>
</body>
</html>
```